Card and board game developer website, small e-commerce site

We are designing a website for Leaping Otter Engine Works. I need a homepage and a typical inside page designed.
The website navigation will be:
Home (where we'll introduce the games and the website)
Our Games (drops open into the two games)
Griffins of Marrowvale
Tidebound
Order Now
About Us
Contact
The header of the website will include the logo, the navigation and a link to a facebook page. The header will also include a cart icon and a link to My Account.
Then on the homepage I suggest we include a row for each game:
Griffins of Marrowvale
This row will include a photo (or maybe a series of photos that animate into each other) and quick info about the game plus two buttons: Info and Photos (which will go to the detail page with the photo gallery), and Order Now (which will take you to the product for ordering).
Tidebound
Your footer will contain a copyright note, plus links to:
Terms and conditions
Shipping and returns
FAQ
Contact
Account login
NOTE: the logo is the orange mokey. I've uploaded a brief with more information. The current website that we are redesigning is here https://www.leapingotterengine.example/
Please send me any questions that you have.
Target Market(s)
People interested in fun card and board games at home.

```html
<!DOCTYPE html>
<html lang="en">
<head>
<meta charset="utf-8">
<title>Leaping Otter Engine Works</title>
<link href="https://fonts.googleapis.com/css2?family=Roboto:wght@400;500;700;900&display=swap" rel="stylesheet">
<style>
:root{
  --orange:#f5841f;
  --black:#000;
  --night:#1c1b1d;
  --white:#fff;
  --footer-text:#5a2c06;
}
*{box-sizing:border-box;margin:0;padding:0}
html,body{width:1200px;height:3087px;overflow:hidden}
body{position:relative;background:var(--black);color:var(--white);font-family:'Roboto',sans-serif}
.abs{position:absolute}
.hero-bg{left:0;top:0;width:1200px;height:620px;background:radial-gradient(ellipse at 50% 35%,#3a3434 0%,#242022 45%,#000 100%)}
.about-bg{left:0;top:2020px;width:1200px;height:710px;background:radial-gradient(ellipse at 50% 45%,#2e2a2b 0%,#1d1b1c 55%,#0a0a0a 100%)}
.brand-badge{left:112px;top:0;width:186px;height:169px;background:var(--white);border-radius:0 0 93px 93px;display:flex;align-items:center;justify-content:center;text-align:center;padding:0 22px 10px}
.brand-name{font-weight:700;font-size:17px;line-height:1.2;color:var(--orange)}
.icon-circle{width:38px;height:38px;border-radius:50%;background:var(--orange);display:flex;align-items:center;justify-content:center}
.util-label{font-size:10px;font-weight:500;color:var(--white)}
.util-value{font-size:18px;font-weight:500;color:var(--white)}
.nav{top:113px;font-size:16px;color:var(--white)}
.caret{display:inline-block;border-left:4px solid transparent;border-right:4px solid transparent;border-top:4px solid var(--white);vertical-align:middle;margin-left:3px}
.btn{display:flex;align-items:center;justify-content:center;border-radius:22px;font-size:17px;font-weight:500;height:42px;width:155px}
.btn-white{background:var(--white);color:var(--orange)}
.btn-ghost-white{border:1.5px solid var(--white);color:var(--white);font-weight:700}
.btn-solid{background:var(--orange);color:var(--white);font-weight:700}
.btn-ghost-orange{border:1.5px solid var(--orange);color:var(--orange);font-weight:700}
.hero-title{left:0;width:1200px;text-align:center;font-weight:700}
.accent{color:var(--orange)}
.section-title{font-size:40px;font-weight:700}
.divider-line{height:1px;background:var(--white)}
.divider-dot{width:10px;height:10px;border-radius:50%;background:var(--orange)}
.game-art{left:112px;width:448px;border-radius:16px}
.game-title{left:639px;font-size:26px;font-weight:700}
.game-copy{left:641px;width:450px;font-size:16.5px;line-height:26px}
.game-copy p{margin-bottom:25px}
.about-copy{left:152px;width:896px;text-align:center;font-size:14px;line-height:30px}
.about-copy p{margin-bottom:30px}
.footer{left:0;top:2730px;width:1200px;height:357px;background:var(--orange)}
.footer-badge{left:504px;top:2757px;width:192px;height:160px;border-radius:50%;background:var(--white);display:flex;align-items:center;justify-content:center;text-align:center;padding:0 24px}
.footer-link{top:2964px;font-size:16px;color:var(--footer-text)}
.copyright{top:3055px;left:0;width:1200px;text-align:center;font-size:13px;color:var(--footer-text)}
</style>
</head>
<body>

<div class="abs hero-bg" role="img" aria-label="Dusky sky scene with airships and floating islands"></div>
<div class="abs about-bg" role="img" aria-label="Faint dark sky scene with airships and floating islands"></div>

<header>
  <div class="abs brand-badge"><span class="brand-name">Leaping Otter Engine Works</span></div>

  <div class="abs icon-circle" style="left:742px;top:48px">
    <svg width="18" height="16" viewBox="0 0 18 16"><path d="M1 2h3l2 8h9l2-6H5" fill="none" stroke="#fff" stroke-width="2"/><circle cx="7" cy="13.5" r="1.5" fill="#fff"/><circle cx="14" cy="13.5" r="1.5" fill="#fff"/></svg>
  </div>
  <div class="abs util-label" style="left:794px;top:49px">CART:</div>
  <div class="abs util-value" style="left:794px;top:64px">$ 0.00</div>

  <div class="abs icon-circle" style="left:882px;top:48px">
    <svg width="18" height="16" viewBox="0 0 18 16"><path d="M1 2h3l2 8h9l2-6H5" fill="none" stroke="#fff" stroke-width="2"/><circle cx="7" cy="13.5" r="1.5" fill="#fff"/><circle cx="14" cy="13.5" r="1.5" fill="#fff"/></svg>
  </div>
  <div class="abs util-label" style="left:934px;top:49px">SIGN IN:</div>
  <div class="abs util-value" style="left:934px;top:64px">ACCOUNT</div>

  <div class="abs icon-circle" style="left:1049px;top:48px" aria-label="Social page link"></div>

  <nav>
    <span class="abs nav" style="left:432px">Home</span>
    <span class="abs nav" style="left:550px">Our Games<span class="caret"></span></span>
    <span class="abs nav" style="left:713px">Order Now<span class="caret"></span></span>
    <span class="abs nav" style="left:873px">About Us</span>
    <span class="abs nav" style="left:1012px">Contact Us</span>
  </nav>
</header>

<section class="hero">
  <h1 class="abs hero-title" style="top:268px;font-size:48px">WELCOME TO</h1>
  <h2 class="abs hero-title accent" style="top:344px;font-size:50px">LEAPING OTTER ENGINE WORKS</h2>
  <a class="abs btn btn-white" style="left:433px;top:439px">Order Now</a>
  <a class="abs btn btn-ghost-white" style="left:614px;top:439px">Contact Us</a>
</section>

<section class="games">
  <h2 class="abs section-title" style="left:110px;top:642px">OUR <span class="accent">GAMES</span></h2>
  <div class="abs divider-line" style="left:112px;top:718px;width:72px"></div>
  <div class="abs divider-dot" style="left:187px;top:713px"></div>
  <div class="abs divider-line" style="left:200px;top:718px;width:72px"></div>
  <a class="abs btn btn-white" style="left:935px;top:667px">Order Now</a>

  <div class="abs game-art" style="top:794px;height:593px;background:linear-gradient(160deg,#7a8a6a 0%,#3c57b0 40%,#5b3ea8 70%,#b25a9a 100%)" role="img" aria-label="Painting of a blue griffin rising above a pink lotus"></div>
  <h3 class="abs game-title" style="top:838px">GRIFFINS OF MARROWVALE</h3>
  <div class="abs game-copy" style="top:898px">
    <p>Welcome to The Griffins Of Marrowvale, the first board game where every player is a GRIFFIN.</p>
    <p>Conquer territory and build your empire.&nbsp; Plunder castles and collect a huge hoard of gold. Rescue relatively attractive royalty or maybe eat them.&nbsp; Who knows?&nbsp; All we know is that everyone's a winner when the pizza's delivered!**</p>
    <p class="accent" style="font-weight:700;font-size:18px">2 - 6 players *</p>
    <p>Playtime approximately 1.5 hours.</p>
    <p>* Game comes with 4 griffin packs.&nbsp; Additional griffin expansion packs coming soon.</p>
  </div>
  <a class="abs btn btn-solid" style="left:641px;top:1296px">Info &amp; Photos</a>
  <a class="abs btn btn-ghost-orange" style="left:817px;top:1296px">Order Now</a>

  <div class="abs game-art" style="top:1492px;height:451px;background:linear-gradient(135deg,#c9c08a 0%,#4f8a6a 35%,#b7a653 60%,#5f9aa5 100%)" role="img" aria-label="Watercolour painting of green, gold and blue landscape"></div>
  <h3 class="abs game-title" style="top:1541px">TIDEBOUND</h3>
  <div class="abs game-copy" style="top:1600px;line-height:30px">
    <p>Welcome to Tidebound, a fast paced card game of strategy and chance.&nbsp; Play your element cards (Earth, Air, Fire,Water) and wild cards (Guardian, Balance, Evolution, Genesis) wisely and be the first player to discard all of their cards and declare yourself the master of the elements.</p>
    <p>Coming to Backerfield soon.</p>
  </div>
  <a class="abs btn btn-solid" style="left:641px;top:1844px">Info &amp; Photos</a>
  <a class="abs btn btn-ghost-orange" style="left:817px;top:1844px">Order Now</a>
</section>

<section class="about">
  <h2 class="abs section-title" style="left:0;width:1200px;text-align:center;top:2140px">ABOUT <span class="accent">LEAPING OTTER ENGINE WORKS</span></h2>
  <div class="abs divider-line" style="left:456px;top:2215px;width:138px"></div>
  <div class="abs divider-dot" style="left:595px;top:2210px"></div>
  <div class="abs divider-line" style="left:607px;top:2215px;width:138px"></div>
  <div class="abs about-copy" style="top:2257px">
    <p>At vero eos et accusamus et iusto odio dignissimos ducimus qui blanditiis praesentium voluptatum deleniti atque corrupti quos dolores et quas molestias excepturi sint occaecati cupiditate non provident, similique sunt in culpa qui officia deserunt mollitia animi, id est laborum et dolorum fuga. Et harum quidem rerum facilis est et expedita distinctio. Nam libero tempore, cum soluta nobis est eligendi optio cumque nihil impedit quo minus id quod maxime placeat facere possimus, omnis voluptas assumenda est, omnis dolor repellendus.</p>
    <p>Temporibus autem quibusdam et aut officiis debitis aut rerum necessitatibus saepe eveniet ut et voluptates repudiandae sint et molestiae non recusandae. Itaque earum rerum hic tenetur a sapiente delectus, ut aut reiciendis voluptatibus maiores alias consequatur aut perferendis doloribus asperiores repellat.At vero eos et accusamus et iusto odio dignissimos ducimus qui blanditiis praesentium voluptatum deleniti atque corrupti quos dolores et quas molestias excepturi sint occaecati cupiditate non provident, similique sunt in culpa qui officia deserunt</p>
  </div>
  <a class="abs btn btn-white" style="left:523px;top:2570px">Read More</a>
</section>

<footer>
  <div class="abs footer"></div>
  <div class="abs footer-badge"><span class="brand-name">Leaping Otter Engine Works</span></div>
  <span class="abs footer-link" style="left:227px">Terms &amp; conditions</span>
  <span class="abs footer-link" style="left:435px">Shipping &amp; Returns</span>
  <span class="abs footer-link" style="left:642px">FAQ</span>
  <span class="abs footer-link" style="left:745px">Contact</span>
  <span class="abs footer-link" style="left:876px">Account Login</span>
  <div class="abs" style="left:581px;top:3001px;width:38px;height:38px;border-radius:50%;background:var(--black)" aria-label="Social page link"></div>
  <div class="abs copyright">(C) Copyright 2024 | All Rights Reserved</div>
</footer>

</body>
</html>
```